Landing Page & Logo for Over 50s Guaranteed Life Cover

www.ripeyearsquote.com provides a method of comparing guaranteed life cover for consumers aged over 50. The approach we are initially looking to deploy is a simple landing page that provides the user with high level information about RipeYearsQuote and allows them to see which provider is offering the best deal by ranking providers in a table. This will compare costs / core features in the same way as shown in the attached file.

The page should incorporate a new logo design for RipeYearsQuote.com which should be similar in design to the website maplegreyhub.com.

Key elements of the landing page include:

Header (incorporating new logo and strapline e.g. "helping you find the best cover at the best price")
Introductory Text (to allow brief description of the service)
Comparison Table (to show top 10 providers - to include logos)
Table Links (allows customer to link directly from the table to the providers site)
Helpline (details of helpline number 0800 617 2948 - not actual number)
Join The Club (allows customers to sign up - using their email - to the over 50s club for more information and offers)

Other design elements welcomed to ensure the landing page is simple to understand, easy to navigate, visually appealing, focused on driving action / sales.
Updates

Target Market(s)

50 - 80

Industry/Entity Type

Insurance

Logo Text

ripeyearsquote and strapline "helping you find the best cover at the best price"

Number of Pages Required

1 page

Font styles to use
Sans Serif

Colors
a5ce39
add136
cadf82
eaf2ce
ffffff

Requirements
Nice to have
• Ideally created so content can be managed via WordPress.

```html
<!DOCTYPE html>
<html lang="en">
<head>
<meta charset="utf-8">
<title>RipeYearsQuote – Over 50s Life Cover Comparison</title>
<link href="https://fonts.googleapis.com/css2?family=Raleway:wght@400;500;600;700&family=Open+Sans:wght@400;600;700&display=swap" rel="stylesheet">
<style>
:root{
  --green:#7cbd1e;
  --green-dark:#5f9c12;
  --lime:#add136;
  --lime-light:#a5ce39;
  --pale:#eaf2ce;
  --ink:#333333;
  --muted:#8a8a8a;
  --line:#e2e2e2;
  --grey-bg:#f1f1f1;
  --table-head:#5a5a5a;
  --white:#ffffff;
  --black:#111111;
}
*{box-sizing:border-box;margin:0;padding:0}
html,body{width:1200px;height:2528px;overflow:hidden}
body{position:relative;background:var(--white);font-family:"Open Sans",sans-serif;color:var(--ink)}
.abs{position:absolute}

/* header */
.site-header{left:0;top:0;width:1200px;height:131px}
.brand{left:180px;top:34px;display:flex;align-items:center;gap:12px}
.brand-dot{width:34px;height:34px;border-radius:50%;background:var(--lime-light)}
.brand-name{font-family:"Raleway",sans-serif;font-weight:600;font-size:36px;color:var(--ink);letter-spacing:.3px}
.brand-strap{left:224px;top:93px;font-size:14px;color:#666}
.helpline{left:851px;top:62px}
.helpline-label{font-size:14px;color:var(--green)}
.helpline-number{display:flex;align-items:center;gap:6px;font-size:21px;color:var(--ink);margin-top:4px}

/* nav */
.main-nav{left:0;top:131px;width:1200px;height:51px;background:linear-gradient(#b4db52,#6aab1c);display:flex;padding-left:180px}
.main-nav a{display:flex;align-items:center;height:51px;padding:0 25px;color:var(--white);font-size:14px;font-weight:600;text-decoration:none;letter-spacing:.3px}
.main-nav a.active{background:var(--black);padding:0 35px}

/* hero */
.hero{left:0;top:182px;width:1200px;height:467px;background:radial-gradient(ellipse at 50% 40%,#c9a791 0%,#8d6e5a 30%,#4e5a3a 65%,#2f3b26 100%);overflow:hidden}
.hero-curve{left:0;bottom:0;width:1200px;height:60px}
.hero-title{left:0;width:1200px;top:132px;text-align:center;font-family:"Raleway",sans-serif;font-size:37px;font-weight:500;color:var(--white);letter-spacing:.5px}
.hero-sub{left:0;width:1200px;top:188px;text-align:center;font-family:"Raleway",sans-serif;font-size:22px;font-weight:500;color:var(--white);letter-spacing:.5px}
.btn-green{background:var(--green);color:var(--white);border-radius:3px;display:flex;align-items:center;justify-content:center;font-weight:600}
.hero-btn{left:537px;top:231px;width:135px;height:34px;font-size:13px}
.hero-dots{left:565px;top:396px;display:flex;gap:4px}
.hero-dots span{width:14px;height:14px;border-radius:50%;background:var(--white)}
.hero-dots span.off{background:transparent;border:2px solid var(--white)}

/* about */
.about-title{left:0;width:1200px;top:658px;text-align:center;font-family:"Raleway",sans-serif;font-size:30px;font-weight:400;color:var(--ink)}
.about-text{left:240px;width:720px;top:712px;text-align:center;font-size:12.5px;line-height:27px;color:#666}
.btn-outline{left:537px;top:807px;width:139px;height:37px;border:2px solid #d8d8d8;display:flex;align-items:center;justify-content:center;font-size:14px;color:#555;font-weight:600}

/* product hexes */
.product-row{left:189px;top:896px;width:822px;height:230px}
.hex{position:absolute;top:0;width:214px;height:230px}
.hex svg.frame{position:absolute;left:0;top:0}
.hex-icon{position:absolute;left:76px;top:30px;width:62px;height:58px;border-radius:14px;background:var(--lime-light)}
.hex-title{position:absolute;left:0;width:214px;top:110px;text-align:center;font-family:"Raleway",sans-serif;font-size:16px;font-weight:500;color:var(--ink)}
.hex-note{position:absolute;left:0;width:214px;top:135px;text-align:center;font-size:11.5px;color:#aaa}
.hex-btn{position:absolute;left:62px;top:161px;width:90px;height:28px;border-radius:14px;background:var(--green);color:var(--white);font-size:11px;display:flex;align-items:center;justify-content:center}
.slider-arrow{width:30px;height:40px;border-radius:50%;background:#e3e3e3;display:flex;align-items:center;justify-content:center}
.arrow-left{left:162px;top:990px;width:34px;height:38px;border-radius:18px 0 0 18px}
.arrow-right{left:1000px;top:990px;width:34px;height:38px;border-radius:0 18px 18px 0}

/* comparison */
.compare-band{left:0;top:1230px;width:1200px;height:763px;background:linear-gradient(160deg,#f4f4f4 0%,#ececec 50%,#f3f3f3 100%)}
.compare-title{left:0;width:1200px;top:1272px;text-align:center;font-family:"Raleway",sans-serif;font-size:24px;color:var(--ink)}
.compare-table{left:234px;top:1330px;width:730px;background:var(--white);border-collapse:collapse}
.compare-table th{background:var(--table-head);color:var(--white);font-size:11px;font-weight:600;height:42px;padding:0}
.compare-table td{height:76px;border-bottom:2px solid var(--line);text-align:center;vertical-align:top;padding-top:16px;font-size:14px;color:#555}
.compare-table td.num small{display:block}
.compare-table td.provider{vertical-align:middle;padding-top:0}
.provider-name{display:inline-flex;align-items:center;gap:7px;font-family:"Raleway",sans-serif;font-weight:700;font-size:17px;color:var(--ink)}
.provider-name i{width:14px;height:14px;background:var(--lime-light);display:inline-block}
.info{display:block;margin:6px auto 0;width:18px;height:18px;border-radius:50%;background:#b5b5b5;color:var(--white);font-size:12px;line-height:18px;font-style:normal;font-weight:700;font-family:Georgia,serif}
.buy{display:block;margin:0 auto;width:72px;height:20px;background:var(--green);color:var(--white);font-size:9px;font-weight:700;line-height:20px}
.more{display:block;margin:7px auto 0;width:72px;height:20px;border:1px solid #bbb;color:#777;font-size:8.5px;font-weight:600;line-height:18px}
.compare-table td.small{font-size:12px}

/* club */
.club{left:0;top:1993px;width:1200px;height:257px;background:linear-gradient(135deg,#4d4d4d 0%,#6b6b6b 45%,#575757 70%,#3f3f3f 100%)}
.club-title{left:0;width:1200px;top:2036px;text-align:center;font-family:"Raleway",sans-serif;font-size:29px;color:var(--white)}
.club-text{left:270px;width:660px;top:2072px;text-align:center;font-size:14px;line-height:26px;color:#f0f0f0}
.club-form{left:399px;top:2147px;width:374px;height:39px;background:var(--white);border:2px solid var(--white);display:flex;align-items:center}
.club-input{flex:1;display:flex;align-items:center;gap:10px;padding-left:12px;font-size:12.5px;color:#aaa}
.club-submit{width:93px;height:35px;background:var(--black);color:var(--white);font-size:12px;font-weight:700;display:flex;align-items:center;justify-content:center}

/* footer */
.site-footer{left:0;top:2250px;width:1200px;height:278px;background:var(--lime)}
.foot-col{top:2294px}
.foot-col h4{font-size:13.5px;font-weight:400;color:var(--white);margin-bottom:16px;letter-spacing:.3px}
.foot-col li{list-style:none;font-size:11.5px;color:var(--white);line-height:25px}
.foot-rule{left:207px;top:2465px;width:843px;height:1px;background:rgba(255,255,255,.6)}
.copyright{left:207px;top:2487px;font-size:10.5px;color:var(--white)}
.social{left:922px;top:2477px;display:flex;gap:6px}
.social span{width:26px;height:26px;border-radius:50%;border:1.5px solid var(--white)}
</style>
</head>
<body>

<header class="site-header abs">
  <div class="brand abs"><span class="brand-dot"></span><span class="brand-name">RipeYearsQuote</span></div>
  <div class="brand-strap abs">helping you find the best cover at the best price</div>
  <div class="helpline abs">
    <div class="helpline-label">Helpline Number</div>
    <div class="helpline-number">
      <svg width="16" height="16" viewBox="0 0 24 24"><path fill="#7cbd1e" d="M6.6 10.8a15.1 15.1 0 0 0 6.6 6.6l2.2-2.2c.3-.3.7-.4 1-.2 1.1.4 2.3.6 3.6.6.6 0 1 .4 1 1V20c0 .6-.4 1-1 1A17 17 0 0 1 3 4c0-.6.4-1 1-1h3.5c.6 0 1 .4 1 1 0 1.3.2 2.5.6 3.6.1.3 0 .7-.2 1z"/></svg>
      0800 617 2948
    </div>
  </div>
</header>

<nav class="main-nav abs">
  <a class="active">HOME</a><a>CAR</a><a>TRAVEL</a><a>PET</a><a>CARAVAN</a><a>LIFE</a><a>HEALTH</a><a>INCOME PROTECTION</a>
</nav>

<section class="hero abs" role="img" aria-label="Photo of a smiling family of four hugging outdoors">
  <div class="hero-title abs">BEST PLANS FOR YOU BEST NEEDS</div>
  <div class="hero-sub abs">VEHICULA PULVINAR ANTE INTEGER</div>
  <div class="hero-btn btn-green abs">Request a Quote</div>
  <div class="hero-dots abs"><span></span><span></span><span></span><span class="off"></span></div>
  <svg class="hero-curve abs" viewBox="0 0 1200 60" preserveAspectRatio="none"><path d="M0 60 Q600 -30 1200 60 Z" fill="#ffffff"/></svg>
</section>

<h2 class="about-title abs">About Our Company</h2>
<p class="about-text abs">A justo id velit placerat molestie Donec dictum lectus non odio Cras a ante vitae enim iaculis aliquam Mauris nunc quam venenatis nec euismod sit amet egestas placerat est Pellentesque habitant morbi tristique senectus et netus et malesuada fames ac turpis egestas Cras id elit Integer quis urna Ut ante enim dapibus malesuada</p>
<div class="btn-outline abs">Learn More</div>

<div class="arrow-left abs slider-arrow"><svg width="12" height="14" viewBox="0 0 12 14"><path d="M9 1 3 7l6 6" stroke="#777" stroke-width="2.5" fill="none"/></svg></div>
<div class="arrow-right abs slider-arrow"><svg width="12" height="14" viewBox="0 0 12 14"><path d="m3 1 6 6-6 6" stroke="#777" stroke-width="2.5" fill="none"/></svg></div>

<div class="product-row abs">
  <div class="hex" style="left:0">
    <svg class="frame" width="214" height="230" viewBox="0 0 214 230"><path d="M107 2 212 58v114L107 228 2 172V58z" fill="#fff" stroke="#dcdcdc" stroke-width="2" stroke-linejoin="round"/></svg>
    <div class="hex-icon" role="img" aria-label="Home insurance icon"></div>
    <div class="hex-title">Home Insurance</div>
    <div class="hex-note">Click below for more info</div>
    <div class="hex-btn">Get a Quote</div>
  </div>
  <div class="hex" style="left:204px">
    <svg class="frame" width="214" height="230" viewBox="0 0 214 230"><path d="M107 2 212 58v114L107 228 2 172V58z" fill="#fff" stroke="#dcdcdc" stroke-width="2" stroke-linejoin="round"/></svg>
    <div class="hex-icon" role="img" aria-label="Car insurance icon"></div>
    <div class="hex-title">Car Insurance</div>
    <div class="hex-note">Click below for more info</div>
    <div class="hex-btn">Get a Quote</div>
  </div>
  <div class="hex" style="left:408px">
    <svg class="frame" width="214" height="230" viewBox="0 0 214 230"><path d="M107 2 212 58v114L107 228 2 172V58z" fill="#fff" stroke="#dcdcdc" stroke-width="2" stroke-linejoin="round"/></svg>
    <div class="hex-icon" role="img" aria-label="Travel insurance icon"></div>
    <div class="hex-title">Travel Insurance</div>
    <div class="hex-note">Click below for more info</div>
    <div class="hex-btn">Get a Quote</div>
  </div>
  <div class="hex" style="left:612px">
    <svg class="frame" width="214" height="230" viewBox="0 0 214 230"><path d="M107 2 212 58v114L107 228 2 172V58z" fill="#fff" stroke="#dcdcdc" stroke-width="2" stroke-linejoin="round"/></svg>
    <div class="hex-icon" role="img" aria-label="Pet insurance icon"></div>
    <div class="hex-title">Pet Insurance</div>
    <div class="hex-note">Click below for more info</div>
    <div class="hex-btn">Get a Quote</div>
  </div>
</div>

<section class="compare-band abs"></section>
<h2 class="compare-title abs">Comparison Table</h2>
<table class="compare-table abs">
  <colgroup><col style="width:123px"><col style="width:98px"><col style="width:97px"><col style="width:93px"><col style="width:109px"><col style="width:108px"><col style="width:102px"></colgroup>
  <thead><tr><th>Company Name</th><th>Cover Amount</th><th>Premium</th><th>Payment Team</th><th>Total Payment</th><th>Intial Period</th><th>Buy Now</th></tr></thead>
  <tbody>
    <tr><td class="provider"><span class="provider-name"><i></i>Norvela</span></td><td>£4,200<i class="info">i</i></td><td class="small">£10.00<i class="info">i</i></td><td class="small">40 Years<i class="info">i</i></td><td class="small">£4,800.00<i class="info">i</i></td><td class="small">24 months<i class="info">i</i></td><td><span class="buy">BUY NOW</span><span class="more">MORE INFO</span></td></tr>
    <tr><td class="provider"><span class="provider-name"><i></i>Calder</span></td><td>£4,200<i class="info">i</i></td><td class="small">£10.00<i class="info">i</i></td><td class="small">40 Years<i class="info">i</i></td><td class="small">£4,800.00<i class="info">i</i></td><td class="small">24 months<i class="info">i</i></td><td><span class="buy">BUY NOW</span><span class="more">MORE INFO</span></td></tr>
    <tr><td class="provider"><span class="provider-name"><i></i>Brightpath</span></td><td>£3,000<i class="info">i</i></td><td class="small">£10.00<i class="info">i</i></td><td class="small">20 Years<i class="info">i</i></td><td class="small">£4,800.00<i class="info">i</i></td><td class="small">24 months<i class="info">i</i></td><td><span class="buy">BUY NOW</span><span class="more">MORE INFO</span></td></tr>
    <tr><td class="provider"><span class="provider-name"><i></i>Haverly</span></td><td>£2,200<i class="info">i</i></td><td class="small">£10.00<i class="info">i</i></td><td class="small">30 Years<i class="info">i</i></td><td class="small">£4,800.00<i class="info">i</i></td><td class="small">24 months<i class="info">i</i></td><td><span class="buy">BUY NOW</span><span class="more">MORE INFO</span></td></tr>
    <tr><td class="provider"><span class="provider-name"><i></i>Ostlund</span></td><td>£2,900<i class="info">i</i></td><td class="small">£10.00<i class="info">i</i></td><td class="small">30 Years<i class="info">i</i></td><td class="small">£4,800.00<i class="info">i</i></td><td class="small">24 months<i class="info">i</i></td><td><span class="buy">BUY NOW</span><span class="more">MORE INFO</span></td></tr>
    <tr><td class="provider"><span class="provider-name" style="font-size:13px"><i></i>Marrow &amp; Finch</span></td><td>£2,600<i class="info">i</i></td><td class="small">£10.00<i class="info">i</i></td><td class="small">20 Years<i class="info">i</i></td><td class="small">£4,800.00<i class="info">i</i></td><td class="small">24 months<i class="info">i</i></td><td><span class="buy">BUY NOW</span><span class="more">MORE INFO</span></td></tr>
    <tr><td class="provider"><span class="provider-name"><i></i>Tessaro</span></td><td>£22,00<i class="info">i</i></td><td class="small">£10.00<i class="info">i</i></td><td class="small">15 Years<i class="info">i</i></td><td class="small">£4,800.00<i class="info">i</i></td><td class="small">24 months<i class="info">i</i></td><td><span class="buy">BUY NOW</span><span class="more">MORE INFO</span></td></tr>
    <tr><td class="provider"><span class="provider-name"><i></i>Fernbrook</span></td><td>£2,100<i class="info">i</i></td><td class="small">£10.00<i class="info">i</i></td><td class="small">10 Years<i class="info">i</i></td><td class="small">£4,800.00<i class="info">i</i></td><td class="small">24 months<i class="info">i</i></td><td><span class="buy">BUY NOW</span><span class="more">MORE INFO</span></td></tr>
  </tbody>
</table>

<section class="club abs" role="img" aria-label="Photo of a desk with laptop, camera, phone and coffee cup from above"></section>
<h2 class="club-title abs">Join the Club</h2>
<p class="club-text abs">Aenean porttitor eros vel dolor Donec convallis pede venenatis nibh Duis quam Nam eget lacus Aliquam erat volutpat Quisque dignissim congue</p>
<div class="club-form abs">
  <div class="club-input">
    <svg width="18" height="13" viewBox="0 0 18 13"><rect x="0.5" y="0.5" width="17" height="12" fill="#cfcfcf"/><path d="M1 1l8 6 8-6" stroke="#fff" stroke-width="1.4" fill="none"/></svg>
    Email address
  </div>
  <div class="club-submit">SIGN UP</div>
</div>

<footer class="site-footer abs"></footer>
<div class="foot-col abs" style="left:207px"><h4>COMPANY</h4><ul><li>Home</li><li>About Us</li><li>Contact Us</li><li>Career Opportunities</li></ul></div>
<div class="foot-col abs" style="left:393px"><h4>SERVICES</h4><ul><li>Home Insurance</li><li>Pet Insurance</li><li>Car Insurance</li><li>Life Insurance</li></ul></div>
<div class="foot-col abs" style="left:519px;top:2326px"><ul><li>Travel Insurance</li><li>Income Protection</li><li>Caravan Protection</li></ul></div>
<div class="foot-col abs" style="left:691px"><h4>RESOURCES</h4><ul><li>Support</li><li>FAQ</li><li>Privacy Policy</li><li>Contact Us</li></ul></div>
<div class="foot-col abs" style="left:846px"><h4>WHY US</h4><ul><li>Larkmere Holdings (HQ)</li><li>Weverstraat 48</li><li>3512 KD Utrecht</li><li>The Netherlands</li></ul></div>
<div class="foot-rule abs"></div>
<div class="copyright abs">© 2016 Company Name. All right reserved. Term of Use</div>
<div class="social abs"><span></span><span></span><span></span><span></span></div>

</body>
</html>
```